Pell Dental Care Small Tote Bag

Pell Dental Care needs an advertisement design for a BrightKart Small Tote Bag. See website "www.pelldental-example.com." See uploaded files for small tote bag design template, color scheme, logos, and photo image of Dr. Pell. Designer may crop photo as necessary.

Target Market(s)

Target market is Adults ages 35 to 80.

Industry/Entity Type

Dental

Font styles to use
Sans Serif

```html
<!DOCTYPE html>
<html lang="en">
<head>
<meta charset="utf-8">
<title>Pell Dental Care – Tote Bag Print</title>
<link rel="stylesheet" href="https://fonts.googleapis.com/css2?family=Lato:wght@400;700;900&display=swap">
<style>
  :root {
    --bg: #d6d6d6;
    --panel-top: #f4f4f4;
    --panel-bottom: #d9dbda;
    --green-dark: #2e4d44;
    --green-deep: #24403a;
    --green-soft: #7fa596;
    --taupe: #7b6b5e;
    --rule: #8a9a94;
    --white: #ffffff;
  }
  * { box-sizing: border-box; margin: 0; padding: 0; }
  html, body {
    width: 1200px; height: 1000px; overflow: hidden;
    background: var(--bg);
    font-family: "Lato", Arial, sans-serif;
  }
  .stage { position: relative; width: 1200px; height: 1000px; }
  .variant { position: absolute; top: 230px; width: 560px; }
  .variant--a { left: 20px; }
  .variant--b { left: 620px; }
  .variant__label {
    position: absolute; top: -62px; left: 0;
    font-size: 44px; font-weight: 900; color: var(--green-dark);
  }
  .print {
    position: relative; width: 560px; height: 560px; overflow: hidden;
    background: linear-gradient(180deg, var(--panel-top), var(--panel-bottom));
    border: 1px solid #9aa09e;
  }
  .brand {
    position: absolute; left: 0; right: 0; top: 0;
    display: flex; align-items: center; justify-content: center;
  }
  .variant--a .brand { height: 258px; }
  .variant--b .brand { height: 318px; }
  .brand__name {
    color: var(--green-dark); font-weight: 700; text-align: center; line-height: 1.05;
  }
  .variant--a .brand__name { font-size: 62px; }
  .variant--b .brand__name { font-size: 70px; }
  .services {
    position: absolute; left: 0; right: 0; top: 258px; height: 54px;
    background: var(--green-dark); color: var(--white);
    display: grid; grid-template-columns: 1fr 1fr; align-content: center;
    padding: 0 64px; row-gap: 2px;
    font-size: 17px; font-weight: 700; letter-spacing: 1px;
  }
  .services li { list-style: none; }
  .services li::before { content: "● "; font-size: 12px; vertical-align: 2px; }
  .contact {
    position: absolute; left: 0; right: 0; top: 322px; height: 88px;
    display: flex; align-items: center; padding-left: 30px;
  }
  .tagline {
    width: 172px; text-align: center; font-size: 18px; font-weight: 700; line-height: 1.4;
    color: var(--taupe);
  }
  .tagline__accent { color: var(--green-soft); }
  .phone-icon { width: 44px; height: 80px; margin: 0 14px 0 12px; }
  .call__lead { font-size: 30px; font-weight: 700; color: var(--green-deep); line-height: 1.1; }
  .call__number { font-size: 39px; font-weight: 900; color: var(--green-deep); line-height: 1.1; }
  .divider {
    position: absolute; left: 30px; right: 30px; top: 420px; height: 1px; background: var(--rule);
  }
  .social {
    position: absolute; left: 18px; right: 18px; top: 428px; height: 42px;
    display: flex; justify-content: space-between; align-items: center;
    font-size: 27px; font-weight: 700; color: var(--green-deep);
  }
  .social__item { display: flex; align-items: center; gap: 8px; }
  .social__dot { width: 26px; height: 26px; border-radius: 50%; background: var(--green-dark); }
  .footer-band { position: absolute; left: 0; bottom: 0; width: 560px; height: 96px; }
  .web {
    position: absolute; left: 0; right: 0; bottom: 14px; text-align: center;
    font-size: 37px; color: var(--white); font-weight: 400;
    text-shadow: 2px 3px 3px rgba(0,0,0,.55);
  }
  .web b { font-weight: 900; }
</style>
</head>
<body>
<main class="stage">

  <section class="variant variant--a">
    <h2 class="variant__label">A</h2>
    <div class="print">
      <div class="brand"><p class="brand__name">Pell<br>Dental Care</p></div>
      <ul class="services">
        <li>General Dentistry</li><li>Beautiful Dentures</li>
        <li>Cosmetic Dentistry</li><li>Sedation Dentistry</li>
      </ul>
      <div class="contact">
        <p class="tagline">Life-Changing<br><span class="tagline__accent">Family Dental Care</span><br>In Brookvale</p>
        <svg class="phone-icon" viewBox="0 0 44 80" aria-hidden="true">
          <rect x="2" y="2" width="40" height="76" rx="6" fill="#2e4d44"/>
          <rect x="8" y="9" width="28" height="26" rx="2" fill="#d9dbda"/>
          <g fill="#d9dbda">
            <rect x="8" y="42" width="7" height="6"/><rect x="18.5" y="42" width="7" height="6"/><rect x="29" y="42" width="7" height="6"/>
            <rect x="8" y="52" width="7" height="6"/><rect x="18.5" y="52" width="7" height="6"/><rect x="29" y="52" width="7" height="6"/>
            <rect x="8" y="62" width="7" height="6"/><rect x="18.5" y="62" width="7" height="6"/><rect x="29" y="62" width="7" height="6"/>
          </g>
        </svg>
        <div class="call"><p class="call__lead">Call Us Today!</p><p class="call__number">(555) 014-2368</p></div>
      </div>
      <div class="divider"></div>
      <div class="social">
        <span class="social__item"><span class="social__dot"></span>Pell Dental Care</span>
        <span class="social__item"><span class="social__dot"></span>@PellDental</span>
      </div>
      <svg class="footer-band" viewBox="0 0 560 96" preserveAspectRatio="none" aria-hidden="true">
        <path d="M0 20 Q280 -6 560 14 L560 96 L0 96 Z" fill="#9fb3ab"/>
        <path d="M0 28 Q280 4 560 22 L560 96 L0 96 Z" fill="#2e4d44"/>
      </svg>
      <p class="web">www.<b>pelldental-example</b>.com</p>
    </div>
  </section>

  <section class="variant variant--b">
    <h2 class="variant__label">B</h2>
    <div class="print">
      <div class="brand"><p class="brand__name">Pell<br>Dental Care</p></div>
      <div class="contact">
        <p class="tagline">Life-Changing<br><span class="tagline__accent">Family Dental Care</span><br>In Brookvale</p>
        <svg class="phone-icon" viewBox="0 0 44 80" aria-hidden="true">
          <rect x="2" y="2" width="40" height="76" rx="6" fill="#2e4d44"/>
          <rect x="8" y="9" width="28" height="26" rx="2" fill="#d9dbda"/>
          <g fill="#d9dbda">
            <rect x="8" y="42" width="7" height="6"/><rect x="18.5" y="42" width="7" height="6"/><rect x="29" y="42" width="7" height="6"/>
            <rect x="8" y="52" width="7" height="6"/><rect x="18.5" y="52" width="7" height="6"/><rect x="29" y="52" width="7" height="6"/>
            <rect x="8" y="62" width="7" height="6"/><rect x="18.5" y="62" width="7" height="6"/><rect x="29" y="62" width="7" height="6"/>
          </g>
        </svg>
        <div class="call"><p class="call__lead">Call Us Today!</p><p class="call__number">(555) 014-2368</p></div>
      </div>
      <div class="divider"></div>
      <div class="social">
        <span class="social__item"><span class="social__dot"></span>Pell Dental Care</span>
        <span class="social__item"><span class="social__dot"></span>@PellDental</span>
      </div>
      <svg class="footer-band" viewBox="0 0 560 96" preserveAspectRatio="none" aria-hidden="true">
        <path d="M0 20 Q280 -6 560 14 L560 96 L0 96 Z" fill="#9fb3ab"/>
        <path d="M0 28 Q280 4 560 22 L560 96 L0 96 Z" fill="#2e4d44"/>
      </svg>
      <p class="web">www.<b>pelldental-example</b>.com</p>
    </div>
  </section>

</main>
</body>
</html>
```